Kestrel Facilities Business Card Design

We would now like to design business cards with the new Kestrel Facilities logo

Target Market(s)

Professional

Industry/Entity Type

Professional services

Contact Information for Business Card

Employee name, title, phone number, email address, corporate office address and logo.

Font styles to use
Sans Serif

Colors
0054AA
0677BA
7BADD7
CADEEF
E8F1F8

Requirements
Must have
• My logo
Should not have
• any other pictures or images besides my logo

```html
<!DOCTYPE html>
<html lang="en">
<head>
<meta charset="utf-8">
<title>Kestrel Facilities Business Card</title>
<link href="https://fonts.googleapis.com/css2?family=Open+Sans:wght@400;700&display=swap" rel="stylesheet">
<style>
  :root {
    --backdrop: #3b3b3b;
    --card: #1b1b1b;
    --card-deep: #111111;
    --blue: #3d84d6;
    --blue-edge: #2f74c4;
    --text-light: #e6e6e6;
  }
  * { box-sizing: border-box; margin: 0; padding: 0; }
  html, body { width: 1200px; height: 801px; overflow: hidden; }
  body {
    background: var(--backdrop);
    font-family: "Open Sans", sans-serif;
    position: relative;
  }
  .card {
    position: absolute;
    top: 252px;
    width: 520px;
    height: 297px;
    background: var(--card);
    border-bottom: 3px solid var(--blue-edge);
    border-left: 2px solid var(--blue-edge);
    box-shadow: 0 18px 40px rgba(0,0,0,0.45);
    overflow: hidden;
  }
  .card-front { left: 50px; }
  .card-back { left: 630px; }

  .front-brand {
    position: absolute;
    left: 0; top: 0;
    width: 250px; height: 100%;
    display: flex;
    align-items: center;
    justify-content: center;
    gap: 10px;
  }
  .brand-square {
    width: 22px; height: 22px;
    background: var(--blue);
    flex: none;
  }
  .brand-name {
    color: var(--blue);
    font-weight: 700;
    font-size: 22px;
    line-height: 1.1;
    text-transform: uppercase;
    letter-spacing: 1px;
  }
  .divider {
    position: absolute;
    left: 262px; top: 58px;
    width: 1.5px; height: 182px;
    background: var(--blue);
  }
  .contact {
    position: absolute;
    left: 282px; top: 62px;
    color: var(--text-light);
    font-size: 13px;
    line-height: 1.55;
  }
  .contact-name {
    color: var(--blue);
    font-weight: 700;
    font-size: 17px;
    text-transform: uppercase;
    letter-spacing: 0.5px;
    line-height: 1.3;
  }
  .contact-title { margin-bottom: 8px; }
  .contact-address { margin-bottom: 8px; }
  .contact-row { display: flex; align-items: center; gap: 7px; }
  .contact-row svg { width: 11px; height: 11px; flex: none; fill: var(--blue); }

  .back-pattern {
    position: absolute;
    inset: 0;
    background: linear-gradient(120deg, #0d0d0d 0%, #1c1c1c 45%, #3a3a3a 70%, #1a1a1a 100%);
  }
  .back-band {
    position: absolute;
    right: 0; top: 112px;
    width: 190px; height: 78px;
    background: var(--card-deep);
    display: flex;
    align-items: center;
    justify-content: center;
    gap: 7px;
  }
  .back-band .brand-name { font-size: 13px; }
  .back-band .brand-square { width: 13px; height: 13px; }
</style>
</head>
<body>
  <section class="card card-front">
    <div class="front-brand">
      <span class="brand-square"></span>
      <span class="brand-name">Kestrel<br>Facilities</span>
    </div>
    <div class="divider"></div>
    <div class="contact">
      <p class="contact-name">Daniel Hargrove</p>
      <p class="contact-title">CEO</p>
      <p class="contact-address">418 Larkspur Avenue<br>Millbrook, MA 02931</p>
      <p class="contact-row">
        <svg viewBox="0 0 24 24"><path d="M6.6 10.8a15 15 0 0 0 6.6 6.6l2.2-2.2a1 1 0 0 1 1-.25 11.4 11.4 0 0 0 3.6.57 1 1 0 0 1 1 1V20a1 1 0 0 1-1 1A17 17 0 0 1 3 4a1 1 0 0 1 1-1h3.5a1 1 0 0 1 1 1c0 1.25.2 2.45.57 3.57a1 1 0 0 1-.25 1z"/></svg>
        555-214-3390
      </p>
      <p class="contact-row">
        <svg viewBox="0 0 24 24"><path d="M2 5h20v14H2z"/><path d="M2 5l10 8 10-8" fill="none" stroke="#1b1b1b" stroke-width="2"/></svg>
        dhargrove@kestrelfacilities.com
      </p>
      <p class="contact-row">
        <svg viewBox="0 0 24 24"><circle cx="12" cy="12" r="10"/></svg>
        www.kestrelfacilities.com
      </p>
    </div>
  </section>

  <section class="card card-back">
    <div class="back-pattern" role="img" aria-label="Glossy spot-varnish pattern of repeated brand monogram on black"></div>
    <div class="back-band">
      <span class="brand-square"></span>
      <span class="brand-name">Kestrel<br>Facilities</span>
    </div>
  </section>
</body>
</html>
```